PowerPoint template for a tech startup

We need a PowerPoint template with a title slide, text slide, section slide, and thank you slide.
Our application helps engineering teams to be more productive. We would love a design that is slick, sophisticated, and consistent with our brand. (see more at www.velmo.ai or attached files)
By the way (not a requirement), Velmo means lighthouse in Greek.
Also, here is the font we used (not required) - https://glyphvault.net/fonts/league-gothic

• https://glyphvault.net/fonts/league-gothic

```html
<!DOCTYPE html>
<html lang="en">
<head>
<meta charset="utf-8">
<title>Velmo – Presentation Template</title>
<link rel="stylesheet" href="https://fonts.googleapis.com/css2?family=League+Gothic&family=Montserrat:wght@400;500;600;700&display=swap">
<style>
:root{
  --navy:#1d4e75;
  --navy-deep:#163f60;
  --orange:#e8591a;
  --purple:#8a6cf0;
  --ink:#3a3f47;
  --muted:#7c828a;
  --line:#d9dce0;
  --page:#d2d3d5;
  --white:#ffffff;
  --grad:linear-gradient(90deg,#1d4e75 0%,#6d4f6e 45%,#e8591a 100%);
}
*{margin:0;padding:0;box-sizing:border-box}
html,body{width:1200px;height:3125px;overflow:hidden}
body{background:var(--page);font-family:"Montserrat",sans-serif;color:var(--ink);position:relative}
.display{font-family:"League Gothic",sans-serif;letter-spacing:.5px;text-transform:uppercase;line-height:1}

/* hero area */
.hero{position:absolute;left:0;top:0;width:1200px;height:728px;background:linear-gradient(180deg,#e6e7ea 0%,#cfd1d5 100%)}
.hero-brand{position:absolute;left:985px;top:52px;font-family:"League Gothic",sans-serif;font-size:96px;color:var(--navy);line-height:1;letter-spacing:1px}
.hero-slide{position:absolute;left:260px;top:160px;transform:scale(1.19);transform-origin:0 0;box-shadow:0 18px 40px rgba(0,0,0,.25)}

/* slide base */
.slide{position:absolute;width:563px;height:316px;background:var(--white);overflow:hidden}
.slide>*{position:absolute}
.brand{font-family:"League Gothic",sans-serif;line-height:1;color:var(--navy);letter-spacing:.5px}
.brand--light{color:var(--white)}
.brand--small{right:22px;top:16px;font-size:28px}
.copyright{font-size:5px;color:var(--muted);left:10px;bottom:12px}
.copyright--center{left:0;right:0;text-align:center;bottom:10px}
.page-no{font-size:5px;color:var(--navy);right:12px;bottom:12px}
.rule-bottom{left:0;right:0;bottom:0;height:3px;background:var(--orange)}
.title-bar{left:0;top:22px;width:8px;height:28px;background:var(--orange)}
.slide-title{left:18px;top:24px;font-size:25px;color:var(--navy)}
.body{font-size:6px;line-height:1.35;color:var(--muted)}
.hl-navy{color:var(--navy);font-weight:700}
.hl-orange{color:var(--orange);font-weight:700}
.hl-purple{color:var(--purple);font-weight:700}
.light{font-weight:400}

/* title slides */
.band{left:0;top:75px;width:563px;height:214px}
.band--grad{background:var(--grad)}
.band--navy{background:var(--navy)}
.title-main{left:53px;top:106px;font-size:31px;color:var(--white);line-height:1.05}
.title-text{left:53px;top:192px;width:330px;font-size:8px;line-height:1.25;color:var(--white)}
.date-pill{left:53px;top:234px;border:1px solid var(--white);border-radius:3px;color:var(--white);font-size:6.5px;padding:5px 14px}

/* table of contents */
.toc-photo{left:0;top:0;width:563px;height:158px;background:linear-gradient(135deg,#2a5e86,#1d4e75 60%,#234f73)}
.toc-brand{left:0;right:0;top:38px;text-align:center;font-size:64px}
.toc-label{left:43px;top:206px;font-size:17px;color:var(--navy);line-height:1.05;text-align:center}
.toc-label b{font-weight:700}
.toc-item{font-size:8px;line-height:1.1}
.toc-item .t{color:var(--orange);font-weight:700}
.toc-item .s{color:var(--orange);font-weight:400}
.toc-item .d{display:block;color:var(--muted);font-size:6px;margin-top:3px}

/* about */
.about-photo{left:35px;top:0;width:261px;height:273px;background:linear-gradient(160deg,#f1f1f1,#cfd0d2 70%,#b9babd)}
.about-title{left:320px;top:72px;font-size:24px;color:var(--navy)}
.about-sub{left:320px;top:98px;font-size:9px;color:var(--orange)}
.about-list{left:320px;top:125px;width:210px;list-style:none}
.about-list li{position:relative;padding-left:14px;font-size:6.5px;line-height:1.3;color:var(--muted);margin-bottom:8px}
.about-list li::before{content:"";position:absolute;left:2px;top:3px;width:3px;height:3px;border-radius:50%;background:var(--orange)}

/* three step */
.step-line{left:0;top:104px;width:530px;height:5px;background:#eef0f2}
.step-line-tip{left:528px;top:98px;width:0;height:0;border-left:10px solid #eef0f2;border-top:8px solid transparent;border-bottom:8px solid transparent}
.step{width:140px;text-align:center;top:82px}
.icon{display:block;margin:0 auto;width:48px;height:48px}
.step h3{margin-top:14px;font-size:12px;line-height:1.15}
.step p{margin-top:8px}

/* section break */
.section-bg{left:0;top:0;width:563px;height:316px}
.section-bg--navy{background:linear-gradient(120deg,#1d4e75,#2a5b82 60%,#1d4e75)}
.section-bg--orange{background:linear-gradient(120deg,#e8591a,#ea6b2c 55%,#d9541a)}
.section-brand{left:53px;top:107px;font-size:46px}
.section-title{left:53px;top:187px;font-size:30px;color:var(--white)}
.section-text{left:53px;top:235px;width:250px;font-size:8px;line-height:1.2;color:var(--white)}

/* list rows */
.row-head{left:39px;width:111px;height:47px;background:var(--navy);color:var(--white);font-size:10px;line-height:1.1;padding:11px 0 0 32px}
.row-head b{font-weight:700}
.row-icon{left:20px;width:34px;height:34px}
.row-box{left:155px;width:384px;height:47px;border:1px solid var(--line);padding:7px 10px 0 18px}
.row-box p{position:relative;font-size:5.2px;line-height:1.25;color:var(--muted);margin-bottom:3px}
.row-box p::before{content:"";position:absolute;left:-8px;top:2px;width:2.5px;height:2.5px;background:var(--orange);border-radius:50%}

/* six features */
.feat{width:150px}
.feat h3{font-size:11px;line-height:1.1}
.feat p{margin-top:3px}
.feat--left{text-align:right;left:68px}
.feat--right{left:344px}
.feat-icon{width:40px;height:40px}

/* chart */
.chart-copy{left:40px;width:205px}
.chart-copy h3{font-size:12px}
.chart-copy p{margin-top:7px}

/* donuts */
.donut{width:150px;text-align:center;top:83px}
.donut h3{margin-top:8px;font-size:12px;font-weight:500}
.donut p{margin-top:6px}

/* contact */
.contact-bg{left:0;top:0;width:563px;height:291px}
.contact-bg--grad{background:var(--grad)}
.contact-bg--navy{background:linear-gradient(120deg,#1d4e75,#24567f 60%,#1d4e75)}
.contact-brand{left:53px;top:87px;font-size:46px}
.contact-title{left:53px;top:163px;font-size:13px;color:var(--white)}
.contact-list{left:53px;top:192px;list-style:none}
.contact-list li{display:flex;align-items:center;gap:7px;font-size:7px;color:var(--white);height:16px}
.contact-list svg{width:9px;height:9px}
</style>
</head>
<body>

<section class="hero">
  <div class="hero-brand">VELMO</div>

  <div class="slide hero-slide">
    <div class="brand" style="left:53px;top:28px;font-size:44px">VELMO</div>
    <div class="band band--grad" role="img" aria-label="Navy to orange band with faint gear line pattern"></div>
    <h1 class="display title-main">The Connected<br>Engineering Operations Platform</h1>
    <p class="title-text">Velmo AI connects the dots between your engineering data sources – ticketing, source control, CI/CD, and more – giving unprecedented visibility and insight into your engineering processes.</p>
    <div class="date-pill">Wednesday, March 9, 2022</div>
    <p class="copyright copyright--center">Copyright © 2022, Velmo AI, Inc. All Rights Reserved.</p>
  </div>
</section>

<!-- title slide, gradient -->
<div class="slide" style="left:28px;top:764px">
  <div class="brand" style="left:53px;top:28px;font-size:44px">VELMO</div>
  <div class="band band--grad" role="img" aria-label="Navy to orange band with faint gear line pattern"></div>
  <h2 class="display title-main">The Connected<br>Engineering Operations Platform</h2>
  <p class="title-text">Velmo AI connects the dots between your engineering data sources – ticketing, source control, CI/CD, and more – giving unprecedented visibility and insight into your engineering processes.</p>
  <div class="date-pill">Wednesday, March 9, 2022</div>
  <p class="copyright copyright--center">Copyright © 2022, Velmo AI, Inc. All Rights Reserved.</p>
</div>

<!-- title slide, navy -->
<div class="slide" style="left:609px;top:764px">
  <div class="brand" style="left:53px;top:28px;font-size:44px">VELMO</div>
  <div class="band band--navy" role="img" aria-label="Navy band with faint gear line pattern"></div>
  <h2 class="display title-main">The Connected<br>Engineering Operations Platform</h2>
  <p class="title-text">Velmo AI connects the dots between your engineering data sources – ticketing, source control, CI/CD, and more – giving unprecedented visibility and insight into your engineering processes.</p>
  <div class="date-pill">Wednesday, March 9, 2022</div>
  <p class="copyright copyright--center">Copyright © 2022, Velmo AI, Inc. All Rights Reserved.</p>
</div>

<!-- table of contents -->
<div class="slide" style="left:28px;top:1099px">
  <div class="toc-photo" role="img" aria-label="Navy tinted photo of a desk with blueprints and a laptop"></div>
  <div class="brand brand--light toc-brand">VELMO</div>
  <p class="toc-label">Table of<br><b>Contents</b></p>
  <p class="toc-item" style="left:164px;top:178px"><span class="t">Your Title</span><br><span class="s">Goes Here</span><span class="d">Consectetur<br>Adipiscing Vivamus</span></p>
  <p class="toc-item" style="left:266px;top:178px"><span class="t">Your Title</span><br><span class="s">Goes Here</span><span class="d">Consectetur<br>Adipiscing Vivamus</span></p>
  <p class="toc-item" style="left:368px;top:178px"><span class="t">Your Title</span><br><span class="s">Goes Here</span><span class="d">Consectetur<br>Adipiscing Vivamus</span></p>
  <p class="toc-item" style="left:470px;top:178px"><span class="t">Your Title</span><br><span class="s">Goes Here</span><span class="d">Consectetur<br>Adipiscing Vivamus</span></p>
  <p class="toc-item" style="left:164px;top:236px"><span class="t">Your Title</span><br><span class="s">Goes Here</span><span class="d">Consectetur<br>Adipiscing Vivamus</span></p>
  <p class="toc-item" style="left:266px;top:236px"><span class="t">Your Title</span><br><span class="s">Goes Here</span><span class="d">Consectetur<br>Adipiscing Vivamus</span></p>
  <p class="toc-item" style="left:368px;top:236px"><span class="t">Your Title</span><br><span class="s">Goes Here</span><span class="d">Consectetur<br>Adipiscing Vivamus</span></p>
  <p class="toc-item" style="left:470px;top:236px"><span class="t">Your Title</span><br><span class="s">Goes Here</span><span class="d">Consectetur<br>Adipiscing Vivamus</span></p>
  <p class="copyright">Copyright © 2022, Velmo AI, Inc. All Rights Reserved.</p>
  <p class="page-no">3</p>
  <div class="rule-bottom"></div>
</div>

<!-- about us -->
<div class="slide" style="left:609px;top:1099px">
  <div class="about-photo" role="img" aria-label="Black and white photo of architectural drawings, drafting tools and glasses"></div>
  <div class="brand brand--small">VELMO</div>
  <h2 class="display about-title">About Us</h2>
  <p class="about-sub">Subtitle Goes Here</p>
  <ul class="about-list">
    <li>Lorem ipsum dolor sit amet, consectetur adipiscing elit. Vivamus eu dui ex. Curabitur dapibus dignissim dui, in molestie metus feugiat sed. Praesent aliquet lorem ex, eu dapibus odio varius at.</li>
    <li>Duis eget tellus porta, consequat lacus vitae, venenatis dolor. Nulla facilisi. In et sollicitudin lacus. Donec risus orci, gravida sit amet risus vehicula, aliquet pretium sapien. Nullam sit amet magna non ex bibendum mollis. Nunc vel neque eu augue dignissim congue ut vitae magna. Phasellus eget commodo arcu.</li>
  </ul>
  <p class="copyright">Copyright © 2022, Velmo AI, Inc. All Rights Reserved.</p>
  <p class="page-no">4</p>
  <div class="rule-bottom"></div>
</div>

<!-- three steps -->
<div class="slide" style="left:28px;top:1434px">
  <div class="title-bar"></div>
  <h2 class="display slide-title">Slide Title Goes Here!</h2>
  <div class="brand brand--small">VELMO</div>
  <div class="step-line"></div>
  <div class="step-line-tip"></div>
  <div class="step" style="left:42px">
    <svg class="icon" viewBox="0 0 48 48"><circle cx="24" cy="24" r="24" fill="#1d4e75"/><circle cx="24" cy="21" r="8" fill="none" stroke="#fff" stroke-width="2.5"/><rect x="20" y="30" width="8" height="6" rx="1" fill="#fff"/></svg>
    <h3 class="hl-navy">Heading<br><span class="light">Goes Here</span></h3>
    <p class="body">Lorem ipsum dolor sit amet, consectetur adipiscing elit. Vivamus eu dui ex. Curabitur dapibus dignissim dui, in molestie metus feugiat sed. Praesent aliquet lorem ex, eu dapibus odio varius at. Duis eget tellus porta, consequat lacus vitae, venenatis dolor.</p>
  </div>
  <div class="step" style="left:212px">
    <svg class="icon" viewBox="0 0 48 48"><circle cx="24" cy="24" r="24" fill="#e8591a"/><circle cx="24" cy="24" r="10" fill="none" stroke="#fff" stroke-width="4" stroke-dasharray="4 2.5"/><circle cx="24" cy="24" r="4" fill="#fff"/></svg>
    <h3 class="hl-orange">Heading<br><span class="light">Goes Here</span></h3>
    <p class="body">Lorem ipsum dolor sit amet, consectetur adipiscing elit. Vivamus eu dui ex. Curabitur dapibus dignissim dui, in molestie metus feugiat sed. Praesent aliquet lorem ex, eu dapibus odio varius at. Duis eget tellus porta, consequat lacus vitae, venenatis dolor.</p>
  </div>
  <div class="step" style="left:382px">
    <svg class="icon" viewBox="0 0 48 48"><circle cx="24" cy="24" r="24" fill="#8a6cf0"/><rect x="15" y="27" width="4" height="8" fill="#fff"/><rect x="22" y="23" width="4" height="12" fill="#fff"/><rect x="29" y="19" width="4" height="16" fill="#fff"/><path d="M14 22 L22 16 L27 19 L34 13" fill="none" stroke="#fff" stroke-width="2"/></svg>
    <h3 class="hl-purple">Heading<br><span class="light">Goes Here</span></h3>
    <p class="body">Lorem ipsum dolor sit amet, consectetur adipiscing elit. Vivamus eu dui ex. Curabitur dapibus dignissim dui, in molestie metus feugiat sed. Praesent aliquet lorem ex, eu dapibus odio varius at. Duis eget tellus porta, consequat lacus vitae, venenatis dolor.</p>
  </div>
  <p class="copyright">Copyright © 2022, Velmo AI, Inc. All Rights Reserved.</p>
  <p class="page-no">5</p>
  <div class="rule-bottom"></div>
</div>

<!-- section break navy -->
<div class="slide" style="left:609px;top:1434px">
  <div class="section-bg section-bg--navy" role="img" aria-label="Navy tinted photo of drafting tools and glasses with faint gear line pattern"></div>
  <div class="brand brand--light section-brand">VELMO</div>
  <h2 class="display section-title">Section Break</h2>
  <p class="section-text">Lorem ipsum dolor sit amet, consectetur adipiscing elit. Vivamus eu dui ex. Curabitur dapibus dignissim dui, in molestie metus feugiat sed.</p>
</div>

<!-- list rows -->
<div class="slide" style="left:28px;top:1769px">
  <div class="title-bar"></div>
  <h2 class="display slide-title">Slide Title Goes Here!</h2>
  <div class="brand brand--small">VELMO</div>

  <div class="row-head" style="top:67px"><b>Heading</b><br>Goes Here</div>
  <svg class="row-icon" style="top:74px" viewBox="0 0 34 34"><circle cx="17" cy="17" r="16" fill="#fff" stroke="#f3c6b1" stroke-width="2"/><circle cx="17" cy="17" r="12" fill="#e8591a"/><circle cx="17" cy="15" r="4.5" fill="none" stroke="#fff" stroke-width="1.6"/><rect x="15" y="20" width="4" height="3" fill="#fff"/></svg>
  <div class="row-box" style="top:67px"><p>Lorem ipsum dolor sit amet, consectetur adipiscing elit. Vivamus eu dui ex. Curabitur dapibus dignissim dui, in molestie metus feugiat sed. Praesent aliquet lorem ex, eu dapibus odio varius at. Duis eget tellus porta, consequat lacus vitae, venenatis dolor.</p><p>Lorem ipsum dolor sit amet, consectetur adipiscing elit. Vivamus eu dui ex. Curabitur dapibus dignissim dui, in molestie metus feugiat sed. Praesent aliquet lorem ex, eu dapibus odio varius at.</p></div>

  <div class="row-head" style="top:141px"><b>Heading</b><br>Goes Here</div>
  <svg class="row-icon" style="top:148px" viewBox="0 0 34 34"><circle cx="17" cy="17" r="16" fill="#fff" stroke="#f3c6b1" stroke-width="2"/><circle cx="17" cy="17" r="12" fill="#e8591a"/><circle cx="17" cy="17" r="5" fill="none" stroke="#fff" stroke-width="2.5" stroke-dasharray="2 1.5"/></svg>
  <div class="row-box" style="top:141px"><p>Lorem ipsum dolor sit amet, consectetur adipiscing elit. Vivamus eu dui ex. Curabitur dapibus dignissim dui, in molestie metus feugiat sed. Praesent aliquet lorem ex, eu dapibus odio varius at. Duis eget tellus porta, consequat lacus vitae, venenatis dolor.</p><p>Lorem ipsum dolor sit amet, consectetur adipiscing elit. Vivamus eu dui ex. Curabitur dapibus dignissim dui, in molestie metus feugiat sed. Praesent aliquet lorem ex, eu dapibus odio varius at.</p></div>

  <div class="row-head" style="top:215px"><b>Heading</b><br>Goes Here</div>
  <svg class="row-icon" style="top:222px" viewBox="0 0 34 34"><circle cx="17" cy="17" r="16" fill="#fff" stroke="#f3c6b1" stroke-width="2"/><circle cx="17" cy="17" r="12" fill="#e8591a"/><rect x="11" y="18" width="3" height="5" fill="#fff"/><rect x="15.5" y="15" width="3" height="8" fill="#fff"/><rect x="20" y="12" width="3" height="11" fill="#fff"/></svg>
  <div class="row-box" style="top:215px"><p>Lorem ipsum dolor sit amet, consectetur adipiscing elit. Vivamus eu dui ex. Curabitur dapibus dignissim dui, in molestie metus feugiat sed. Praesent aliquet lorem ex, eu dapibus odio varius at. Duis eget tellus porta, consequat lacus vitae, venenatis dolor.</p><p>Lorem ipsum dolor sit amet, consectetur adipiscing elit. Vivamus eu dui ex. Curabitur dapibus dignissim dui, in molestie metus feugiat sed. Praesent aliquet lorem ex, eu dapibus odio varius at.</p></div>

  <p class="copyright">Copyright © 2022, Velmo AI, Inc. All Rights Reserved.</p>
  <p class="page-no">7</p>
  <div class="rule-bottom"></div>
</div>

<!-- six features -->
<div class="slide" style="left:609px;top:1769px">
  <div class="title-bar"></div>
  <h2 class="display slide-title">Slide Title Goes Here!</h2>
  <div class="brand brand--small">VELMO</div>

  <div class="feat feat--left" style="top:91px"><h3 class="hl-navy">Heading <span class="light">Goes Here</span></h3><p class="body">Lorem ipsum dolor sit amet, consectetur adipiscing elit. Vivamus eu dui ex. Curabitur dapibus dignissim.</p></div>
  <div class="feat feat--left" style="top:153px"><h3 class="hl-orange">Heading <span class="light">Goes Here</span></h3><p class="body">Lorem ipsum dolor sit amet, consectetur adipiscing elit. Vivamus eu dui ex. Curabitur dapibus dignissim.</p></div>
  <div class="feat feat--left" style="top:215px"><h3 class="hl-navy">Heading <span class="light">Goes Here</span></h3><p class="body">Lorem ipsum dolor sit amet, consectetur adipiscing elit. Vivamus eu dui ex. Curabitur dapibus dignissim.</p></div>

  <svg class="feat-icon" style="left:232px;top:89px" viewBox="0 0 40 40"><circle cx="20" cy="20" r="20" fill="#1d4e75"/><circle cx="20" cy="18" r="6" fill="none" stroke="#fff" stroke-width="2"/><rect x="17" y="25" width="6" height="4" fill="#fff"/></svg>
  <svg class="feat-icon" style="left:232px;top:151px" viewBox="0 0 40 40"><circle cx="20" cy="20" r="20" fill="#e8591a"/><path d="M14 12 L26 28 M26 12 L14 28" stroke="#fff" stroke-width="3" stroke-linecap="round"/></svg>
  <svg class="feat-icon" style="left:232px;top:213px" viewBox="0 0 40 40"><circle cx="20" cy="20" r="20" fill="#1d4e75"/><ellipse cx="16" cy="17" rx="6" ry="4" fill="none" stroke="#fff" stroke-width="2"/><ellipse cx="24" cy="23" rx="6" ry="4" fill="none" stroke="#fff" stroke-width="2"/></svg>
  <svg class="feat-icon" style="left:293px;top:89px" viewBox="0 0 40 40"><circle cx="20" cy="20" r="20" fill="#e8591a"/><circle cx="20" cy="20" r="9" fill="none" stroke="#fff" stroke-width="4" stroke-dasharray="3.5 2.5"/><circle cx="20" cy="20" r="3.5" fill="#fff"/></svg>
  <svg class="feat-icon" style="left:293px;top:151px" viewBox="0 0 40 40"><circle cx="20" cy="20" r="20" fill="#1d4e75"/><circle cx="20" cy="20" r="10" fill="none" stroke="#fff" stroke-width="2"/><path d="M20 14 V20 H25" fill="none" stroke="#fff" stroke-width="2"/></svg>
  <svg class="feat-icon" style="left:293px;top:213px" viewBox="0 0 40 40"><circle cx="20" cy="20" r="20" fill="#e8591a"/><rect x="12" y="22" width="4" height="7" fill="#fff"/><rect x="18" y="18" width="4" height="11" fill="#fff"/><rect x="24" y="14" width="4" height="15" fill="#fff"/></svg>

  <div class="feat feat--right" style="top:89px"><h3 class="hl-orange">Heading <span class="light">Goes Here</span></h3><p class="body">Lorem ipsum dolor sit amet, consectetur adipiscing elit. Vivamus eu dui ex. Curabitur dapibus dignissim.</p></div>
  <div class="feat feat--right" style="top:151px"><h3 class="hl-navy">Heading <span class="light">Goes Here</span></h3><p class="body">Lorem ipsum dolor sit amet, consectetur adipiscing elit. Vivamus eu dui ex. Curabitur dapibus dignissim.</p></div>
  <div class="feat feat--right" style="top:213px"><h3 class="hl-orange">Heading <span class="light">Goes Here</span></h3><p class="body">Lorem ipsum dolor sit amet, consectetur adipiscing elit. Vivamus eu dui ex. Curabitur dapibus dignissim.</p></div>

  <p class="copyright">Copyright © 2022, Velmo AI, Inc. All Rights Reserved.</p>
  <p class="page-no">8</p>
  <div class="rule-bottom"></div>
</div>

<!-- section break orange -->
<div class="slide" style="left:28px;top:2104px">
  <div class="section-bg section-bg--orange" role="img" aria-label="Orange tinted photo of hands working at a tablet with faint gear line pattern"></div>
  <div class="brand brand--light section-brand">VELMO</div>
  <h2 class="display section-title">Section Break</h2>
  <p class="section-text">Lorem ipsum dolor sit amet, consectetur adipiscing elit. Vivamus eu dui ex. Curabitur dapibus dignissim dui, in molestie metus feugiat sed.</p>
</div>

<!-- chart -->
<div class="slide" style="left:609px;top:2104px">
  <div class="title-bar"></div>
  <h2 class="display slide-title">Slide Title Goes Here</h2>
  <div class="brand brand--small">VELMO</div>
  <div class="chart-copy" style="top:90px"><h3 class="hl-navy">Heading <span class="light">Goes Here</span></h3><p class="body">Lorem ipsum dolor sit amet, consectetur adipiscing elit. Vivamus eu dui ex. Curabitur dapibus dignissim dui, in molestie metus feugiat sed.</p></div>
  <div class="chart-copy" style="top:151px"><h3 class="hl-orange">Heading <span class="light">Goes Here</span></h3><p class="body">Lorem ipsum dolor sit amet, consectetur adipiscing elit. Vivamus eu dui ex. Curabitur dapibus dignissim dui, in molestie metus feugiat sed.</p></div>
  <div class="chart-copy" style="top:212px"><h3 class="hl-purple">Heading <span class="light">Goes Here</span></h3><p class="body">Lorem ipsum dolor sit amet, consectetur adipiscing elit. Vivamus eu dui ex. Curabitur dapibus dignissim dui, in molestie metus feugiat sed.</p></div>
  <svg style="left:270px;top:95px" width="260" height="170" viewBox="0 0 260 170" role="img" aria-label="Grouped bar chart for A, B and C">
    <g stroke="#eceef0" stroke-width="1"><line x1="2" y1="0" x2="2" y2="150"/><line x1="84" y1="0" x2="84" y2="150"/><line x1="166" y1="0" x2="166" y2="150"/><line x1="248" y1="0" x2="248" y2="150"/><line x1="2" y1="150" x2="248" y2="150"/></g>
    <g font-family="Montserrat, sans-serif" font-size="5" fill="#7c828a" text-anchor="middle">
      <rect x="26" y="21" width="9" height="129" fill="#1d4e75"/><rect x="38" y="78" width="9" height="72" fill="#e8591a"/><rect x="50" y="90" width="9" height="60" fill="#8a6cf0"/>
      <text x="30" y="16" transform="rotate(-90 30 16)">4.3</text><text x="42" y="73" transform="rotate(-90 42 73)">2.4</text><text x="54" y="85" transform="rotate(-90 54 85)">2</text>
      <rect x="108" y="75" width="9" height="75" fill="#1d4e75"/><rect x="120" y="18" width="9" height="132" fill="#e8591a"/><rect x="132" y="90" width="9" height="60" fill="#8a6cf0"/>
      <text x="112" y="70" transform="rotate(-90 112 70)">2.5</text><text x="124" y="13" transform="rotate(-90 124 13)">4.4</text><text x="136" y="85" transform="rotate(-90 136 85)">2</text>
      <rect x="190" y="45" width="9" height="105" fill="#1d4e75"/><rect x="202" y="96" width="9" height="54" fill="#e8591a"/><rect x="214" y="60" width="9" height="90" fill="#8a6cf0"/>
      <text x="194" y="40" transform="rotate(-90 194 40)">3.5</text><text x="206" y="91" transform="rotate(-90 206 91)">1.8</text><text x="218" y="55" transform="rotate(-90 218 55)">3</text>
      <text x="42" y="160">A</text><text x="124" y="160">B</text><text x="206" y="160">C</text>
    </g>
  </svg>
  <p class="copyright">Copyright © 2022, Velmo AI, Inc. All Rights Reserved.</p>
  <p class="page-no">10</p>
  <div class="rule-bottom"></div>
</div>

<!-- donuts -->
<div class="slide" style="left:28px;top:2439px">
  <div class="title-bar"></div>
  <h2 class="display slide-title">Slide Title Goes Here</h2>
  <div class="brand brand--small">VELMO</div>
  <div class="donut" style="left:50px">
    <svg width="120" height="120" viewBox="0 0 120 120"><circle cx="60" cy="60" r="54" fill="none" stroke="#1d4e75" stroke-width="6" stroke-dasharray="217 340" transform="rotate(-90 60 60)"/><text x="60" y="68" text-anchor="middle" font-family="Montserrat, sans-serif" font-size="26" fill="#1d4e75">64<tspan font-size="13">%</tspan></text></svg>
    <h3 style="color:var(--navy)">Heading</h3>
    <p class="body">Lorem ipsum dolor sit amet, consectetur adipiscing elit. Vivamus eu dui ex. Curabitur dapibus dignissim dui.</p>
  </div>
  <div class="donut" style="left:207px">
    <svg width="120" height="120" viewBox="0 0 120 120"><circle cx="60" cy="60" r="54" fill="none" stroke="#e8591a" stroke-width="6" stroke-dasharray="278 340" transform="rotate(-90 60 60)"/><text x="60" y="68" text-anchor="middle" font-family="Montserrat, sans-serif" font-size="26" fill="#e8591a">82<tspan font-size="13">%</tspan></text></svg>
    <h3 style="color:var(--orange)">Heading</h3>
    <p class="body">Lorem ipsum dolor sit amet, consectetur adipiscing elit. Vivamus eu dui ex. Curabitur dapibus dignissim dui.</p>
  </div>
  <div class="donut" style="left:363px">
    <svg width="120" height="120" viewBox="0 0 120 120"><circle cx="60" cy="60" r="54" fill="none" stroke="#8a6cf0" stroke-width="6" stroke-dasharray="319 340" transform="rotate(-90 60 60)"/><text x="60" y="68" text-anchor="middle" font-family="Montserrat, sans-serif" font-size="26" fill="#8a6cf0">94<tspan font-size="13">%</tspan></text></svg>
    <h3 style="color:var(--purple)">Heading</h3>
    <p class="body">Lorem ipsum dolor sit amet, consectetur adipiscing elit. Vivamus eu dui ex. Curabitur dapibus dignissim dui.</p>
  </div>
  <p class="copyright">Copyright © 2022, Velmo AI, Inc. All Rights Reserved.</p>
  <p class="page-no">11</p>
  <div class="rule-bottom"></div>
</div>

<!-- contact gradient -->
<div class="slide" style="left:609px;top:2439px">
  <div class="contact-bg contact-bg--grad" role="img" aria-label="Navy to orange tinted photo of a business handshake with faint gear line pattern"></div>
  <div class="brand brand--light contact-brand">VELMO</div>
  <h2 class="display contact-title">Contact Us</h2>
  <ul class="contact-list">
    <li><svg viewBox="0 0 10 10"><path d="M2 1 L4 1 L5 3 L4 4 Q5 6 6 6 L7 5 L9 6 L9 8 Q8 9 7 9 Q1 8 1 2 Q1 1 2 1Z" fill="#fff"/></svg>Insert Phone Number</li>
    <li><svg viewBox="0 0 10 10"><circle cx="5" cy="5" r="4" fill="none" stroke="#fff" stroke-width="1"/><circle cx="5" cy="5" r="1.6" fill="none" stroke="#fff" stroke-width="1"/></svg>Insert E-Mail Address</li>
    <li><svg viewBox="0 0 10 10"><circle cx="5" cy="5" r="4" fill="none" stroke="#fff" stroke-width="1"/><ellipse cx="5" cy="5" rx="1.8" ry="4" fill="none" stroke="#fff" stroke-width=".8"/><line x1="1" y1="5" x2="9" y2="5" stroke="#fff" stroke-width=".8"/></svg>Insert URL Address</li>
  </ul>
  <p class="copyright copyright--center">Copyright © 2022, Velmo AI, Inc. All Rights Reserved.</p>
</div>

<!-- contact navy -->
<div class="slide" style="left:319px;top:2774px">
  <div class="contact-bg contact-bg--navy" role="img" aria-label="Navy tinted photo of a business handshake with faint gear line pattern"></div>
  <div class="brand brand--light contact-brand">VELMO</div>
  <h2 class="display contact-title">Contact Us</h2>
  <ul class="contact-list">
    <li><svg viewBox="0 0 10 10"><path d="M2 1 L4 1 L5 3 L4 4 Q5 6 6 6 L7 5 L9 6 L9 8 Q8 9 7 9 Q1 8 1 2 Q1 1 2 1Z" fill="#fff"/></svg>Insert Phone Number</li>
    <li><svg viewBox="0 0 10 10"><circle cx="5" cy="5" r="4" fill="none" stroke="#fff" stroke-width="1"/><circle cx="5" cy="5" r="1.6" fill="none" stroke="#fff" stroke-width="1"/></svg>Insert E-Mail Address</li>
    <li><svg viewBox="0 0 10 10"><circle cx="5" cy="5" r="4" fill="none" stroke="#fff" stroke-width="1"/><ellipse cx="5" cy="5" rx="1.8" ry="4" fill="none" stroke="#fff" stroke-width=".8"/><line x1="1" y1="5" x2="9" y2="5" stroke="#fff" stroke-width=".8"/></svg>Insert URL Address</li>
  </ul>
  <p class="copyright copyright--center">Copyright © 2022, Velmo AI, Inc. All Rights Reserved.</p>
</div>

</body>
</html>
```